Full Page Color Ad

We need a full page 8.5 x 11 ad created for a magazine. Please see the attached examples. It would be best if the wording/style stayed the same. As far as background image, we are looking for something catchy that portrays "hidden treasure". Please be sure to include the logos as well. If you have any questions or need anything else, please email mhorvent@tarquill.com You can also visit www.tarquill.com to learn at little about our company and see our branding/style.
*Please follow the style and wording of the examples as best as possible. Not looking for variation on the text layout- more ofthe background and added creativity.*
Industry/Entity Type
It Company
Look and feel

```html
<!DOCTYPE html>
<html lang="en">
<head>
<meta charset="utf-8">
<title>Discover Hidden Value – Tarquill</title>
<link href="https://fonts.googleapis.com/css2?family=Anton&family=Oswald:wght@700&family=Arimo:wght@400;700&display=swap" rel="stylesheet">
<style>
  :root {
    --ink: #000000;
    --paper: #ffffff;
    --accent: #f6a623;
    --brand-blue: #1a3a8c;
    --badge-blue: #2a67b8;
    --badge-light: #5aa3dc;
    --glow: #8a5a2a;
    --floor: #c98a45;
    --body-text: #1a1a1a;
  }
  html, body {
    margin: 0;
    padding: 0;
    width: 900px;
    height: 1200px;
    overflow: hidden;
    background: var(--paper);
  }
  .ad {
    position: relative;
    width: 900px;
    height: 1200px;
    overflow: hidden;
  }
  .hero {
    position: absolute;
    inset: 0 0 auto 0;
    height: 961px;
    background: var(--ink);
    overflow: hidden;
  }
  .hero-visual {
    position: absolute;
    left: 0;
    right: 0;
    top: 560px;
    height: 401px;
    background:
      radial-gradient(ellipse 52% 42% at 50% 62%, rgba(240,170,90,0.95) 0%, rgba(201,138,69,0.75) 35%, rgba(120,70,30,0.45) 65%, rgba(0,0,0,0) 100%),
      radial-gradient(ellipse 22% 24% at 48% 40%, rgba(90,40,20,0.9) 0%, rgba(0,0,0,0) 100%),
      var(--ink);
  }
  .headline {
    position: absolute;
    left: 44px;
    top: 42px;
    margin: 0;
    font-family: "Anton", "Oswald", sans-serif;
    font-weight: 400;
    font-size: 94px;
    line-height: 1.1;
    letter-spacing: 0.5px;
    color: var(--paper);
    white-space: nowrap;
  }
  .headline .highlight { color: var(--accent); }
  .lead-in {
    position: absolute;
    left: 48px;
    top: 176px;
    margin: 0;
    font-family: "Oswald", sans-serif;
    font-weight: 700;
    font-size: 56px;
    line-height: 70px;
    color: var(--paper);
  }
  .process-list {
    position: absolute;
    left: 200px;
    top: 166px;
    margin: 0;
    padding: 0;
    list-style: none;
    font-family: "Oswald", sans-serif;
    font-weight: 700;
    font-size: 32px;
    line-height: 43.5px;
    color: var(--paper);
    letter-spacing: 0.2px;
  }
  .process-list .featured { color: var(--accent); }
  .closer {
    position: absolute;
    left: 534px;
    top: 330px;
    margin: 0;
    font-family: "Oswald", sans-serif;
    font-weight: 700;
    font-size: 82px;
    line-height: 1.1;
    color: var(--paper);
  }
  .footer {
    position: absolute;
    left: 0;
    right: 0;
    bottom: 0;
    height: 239px;
    background: var(--paper);
  }
  .brand {
    position: absolute;
    left: 42px;
    top: 53px;
    display: flex;
    align-items: center;
    gap: 8px;
  }
  .brand-square {
    width: 26px;
    height: 26px;
    background: var(--brand-blue);
  }
  .brand-name {
    font-family: "Arimo", sans-serif;
    font-weight: 700;
    font-size: 24px;
    color: var(--brand-blue);
  }
  .blurb {
    position: absolute;
    left: 187px;
    top: 56px;
    width: 480px;
    margin: 0;
    font-family: "Arimo", Arial, sans-serif;
    font-size: 15px;
    line-height: 21px;
    color: var(--body-text);
  }
  .partner-badge {
    position: absolute;
    left: 691px;
    top: 53px;
    width: 178px;
    height: 112px;
  }
</style>
</head>
<body>
<main class="ad">
  <section class="hero">
    <div class="hero-visual" role="img" aria-label="Antique wooden treasure chest lit by a warm spotlight on a wooden floor"></div>
    <h1 class="headline">Discover <span class="highlight">Hidden</span> Value</h1>
    <p class="lead-in">FROM<br>YOUR</p>
    <ul class="process-list">
      <li>CONSOLIDATIONS</li>
      <li>FINANCIAL PLANNING</li>
      <li>STRATEGY MANAGEMENT</li>
      <li>PROFITABILITY</li>
      <li class="featured">PERFORMANCE</li>
      <li class="featured">MANAGEMENT</li>
      <li>BALANCED SCORECARD</li>
      <li>SALES &amp; OPERATIONS</li>
      <li>PLANNING</li>
    </ul>
    <p class="closer">PROCESS.</p>
  </section>
  <footer class="footer">
    <div class="brand">
      <span class="brand-square"></span>
      <span class="brand-name">tarquill</span>
    </div>
    <p class="blurb">Tarquill is trusted by more companies globally to deliver high value solutions featuring Nexora’s Business Analytics portfolio. Our team offers visionary services that maximize the business value your company can realize from these powerful products. Contact us today for more information.</p>
    <svg class="partner-badge" viewBox="0 0 178 112" aria-hidden="true">
      <rect x="0" y="0" width="178" height="112" fill="var(--badge-blue)"/>
      <rect x="60" y="60" width="118" height="52" fill="var(--badge-light)"/>
    </svg>
  </footer>
</main>
</body>
</html>
```